Business Card for premium dental clinic

We are a premium dental clinic based in Brasov, Romania with more than 15 year on the market, providing quality dental treatment made by a team of more specialized dentists, working with modern equipment as a solution to beautiful and healthy teeth.

Our current logo for the clinic use 2 square with colors black and gold - dr Ternisu - studio, using family fonts Bodoni, Myriad Pro and Segoe Print.
Depending on the printing we used some gold CMYK background or gold foil picture background or a gold gradient.
We want a business card:
- eye catching business card
- distinguished business card
- premium design
- to keep the color scheme of black and gold
- to attract the customers to spent time reading the information
- modern concept

```html
<!DOCTYPE html>
<html lang="en">
<head>
<meta charset="utf-8">
<title>Aurel Dental Clinic – Business Card</title>
<link rel="stylesheet" href="https://fonts.googleapis.com/css2?family=Montserrat:wght@500&family=Saira+Condensed:wght@300&display=swap">
<style>
  :root {
    --backdrop: #3b312c;
    --card: #2a2b2d;
    --gloss: #141516;
    --gloss-soft: #1b1c1e;
    --gold: #c9a13b;
    --divider: #3c3d40;
  }
  * { box-sizing: border-box; margin: 0; padding: 0; }
  html, body {
    width: 1200px; height: 800px; overflow: hidden;
    background: var(--backdrop);
  }
  .stage {
    width: 1200px; height: 800px;
    display: flex; align-items: center; justify-content: center; gap: 60px;
  }
  .card {
    position: relative;
    width: 520px; height: 300px;
    background: var(--card);
    border: 2px solid var(--gold);
    box-shadow: 0 18px 40px rgba(0,0,0,.45);
    overflow: hidden;
  }

  /* Front */
  .card--front { display: flex; align-items: center; justify-content: center; }
  .brand {
    display: flex; align-items: center; gap: 18px;
    transform: translateY(-10px);
  }
  .brand__mark {
    width: 22px; height: 22px; border-radius: 50%;
    background: var(--gloss);
  }
  .brand__name {
    font-family: "Montserrat", sans-serif;
    font-weight: 500;
    font-size: 38px;
    letter-spacing: 1px;
    color: var(--gloss);
    text-transform: lowercase;
    line-height: 1.1;
  }
  .brand__name span { display: block; font-size: 15px; letter-spacing: 3px; text-transform: uppercase; }

  /* Back */
  .card--back { display: flex; align-items: center; padding-left: 54px; }
  .doctor {
    font-family: "Saira Condensed", sans-serif;
    font-weight: 300;
    font-size: 54px;
    color: var(--gloss);
    letter-spacing: .5px;
    white-space: nowrap;
  }
  .doctor small { font-size: 30px; margin-right: 4px; }
  .divider {
    width: 1px; height: 90px;
    background: var(--divider);
    margin: 0 26px 0 28px;
  }
  .contact { list-style: none; display: flex; flex-direction: column; gap: 8px; }
  .contact li {
    display: flex; align-items: center; gap: 10px;
    font-family: "Montserrat", sans-serif;
    font-weight: 500; font-size: 13px;
    color: var(--gloss);
  }
  .contact svg { width: 13px; height: 13px; fill: var(--gloss); flex: none; }
</style>
</head>
<body>
<main class="stage">
  <section class="card card--front" aria-label="Card front">
    <div class="brand">
      <div class="brand__mark"></div>
      <div class="brand__name">aurel<span>dental clinic</span></div>
    </div>
  </section>

  <section class="card card--back" aria-label="Card back">
    <h1 class="doctor"><small>dr.</small>ternisu</h1>
    <div class="divider"></div>
    <ul class="contact">
      <li>
        <svg viewBox="0 0 24 24" aria-hidden="true"><path d="M6.6 10.8a15.1 15.1 0 0 0 6.6 6.6l2.2-2.2a1 1 0 0 1 1-.25 11.4 11.4 0 0 0 3.6.57 1 1 0 0 1 1 1V20a1 1 0 0 1-1 1A17 17 0 0 1 3 4a1 1 0 0 1 1-1h3.5a1 1 0 0 1 1 1c0 1.25.2 2.45.57 3.57a1 1 0 0 1-.25 1z"/></svg>
        0268-555-210
      </li>
      <li>
        <svg viewBox="0 0 24 24" aria-hidden="true"><path d="M2 5h20v14H2z M4 7v.5l8 5 8-5V7l-8 5z" fill-rule="evenodd"/></svg>
        hello@aureldental.ro
      </li>
      <li>
        <svg viewBox="0 0 24 24" aria-hidden="true"><path d="M12 2a10 10 0 1 0 0 20 10 10 0 0 0 0-20zm6.9 9h-3a15 15 0 0 0-1.4-6A8 8 0 0 1 18.9 11zM12 4.1c.9 1.2 1.7 3.6 1.9 6.9h-3.8c.2-3.3 1-5.7 1.9-6.9zM9.5 5a15 15 0 0 0-1.4 6h-3A8 8 0 0 1 9.5 5zM5.1 13h3a15 15 0 0 0 1.4 6A8 8 0 0 1 5.1 13zM12 19.9c-.9-1.2-1.7-3.6-1.9-6.9h3.8c-.2 3.3-1 5.7-1.9 6.9zm2.5-.9a15 15 0 0 0 1.4-6h3a8 8 0 0 1-4.4 6z"/></svg>
        www.aureldental.ro
      </li>
    </ul>
  </section>
</main>
</body>
</html>
```